Travel Agency Website - Simple General

Need a 7 page simple design that is pretty repetitive. Need to be able to load quickly that is SEO optimized. Trying to give ideas on what they can do, be personal as we are local, but at the same time come across as professional and get information easily with little burden.

- Landing Page
- Brimwell Vacations Page
- Family Trips
- Road Trips from Texas
- Other Destinations
- About Us Page
- Contact Us Page

Target Market(s)

Families

Coding

Coded - Design and coding required

Number of Pages Required

5+ page

Colors

Designer to choose colors to be used in the design.

Requirements
Must have
• Like it to flow easily with our logo. Use that for colors, etc.

```html
<!DOCTYPE html>
<html lang="en">
<head>
<meta charset="utf-8">
<title>Hum Along As You Roam Travel Co.</title>
<link href="https://fonts.googleapis.com/css2?family=Montserrat:wght@400;500;600&family=Great+Vibes&family=Dancing+Script:wght@500&display=swap" rel="stylesheet">
<style>
:root{
  --teal:#1e6f6c;
  --teal-dark:#17605d;
  --gold:#c9a444;
  --ink:#333;
  --muted:#555;
  --white:#fff;
}
*{box-sizing:border-box;margin:0;padding:0}
html,body{width:1200px;height:2627px;overflow:hidden}
body{position:relative;font-family:'Montserrat',sans-serif;color:var(--ink);background:var(--white)}
a{text-decoration:none;color:inherit}
.abs{position:absolute}

.topbar{left:0;top:0;width:1200px;height:30px;background:var(--teal);color:var(--white);font-size:13px}
.topbar .contact{left:125px;top:7px;display:flex;gap:16px;align-items:center}
.topbar .contact span{display:flex;align-items:center;gap:6px}
.topbar .social{right:125px;top:7px;display:flex;gap:14px}

.header{left:0;top:30px;width:1200px;height:108px;background:var(--white)}
.brand{left:125px;top:62px;display:flex;align-items:center;gap:8px;color:var(--teal);font-size:15px;font-weight:600;width:120px;line-height:1.2}
.brand .dot{width:14px;height:14px;border-radius:50%;background:var(--gold);flex:none}
.nav{left:410px;top:75px;display:flex;gap:27px;font-size:13.5px;letter-spacing:1.6px;color:var(--ink)}
.nav a.active{color:var(--teal);font-weight:600;border-bottom:2px solid var(--gold);padding:0 12px 6px;margin-left:-12px;margin-right:-12px}

.hero{left:0;top:138px;width:1200px;height:720px;background:linear-gradient(180deg,#5a938d 0%,#3f7f7a 45%,#2c7670 70%,#1f6f6b 100%);color:var(--white);text-align:center}
.hero .eyebrow{position:absolute;left:0;width:1200px;top:141px;font-size:14px;letter-spacing:4px;font-weight:500}
.hero .rule{position:absolute;left:583px;width:34px;height:1px;background:rgba(255,255,255,.7)}
.hero h1{position:absolute;left:0;width:1200px;top:196px;font-family:'Great Vibes',cursive;font-weight:400;font-size:106px;line-height:104px}
.hero .sub{position:absolute;left:0;width:1200px;top:415px;font-size:13px;letter-spacing:4px;font-weight:500}
.hero p{position:absolute;left:310px;width:580px;top:455px;font-size:16.5px;line-height:28px}
.btn{display:inline-block;background:var(--gold);color:var(--teal);border-radius:24px;font-weight:600;letter-spacing:2.6px;font-size:16px;text-align:center}
.hero .btn{position:absolute;left:442px;top:542px;width:317px;height:43px;line-height:43px}
.wave{left:0;top:818px;width:1200px;height:42px}

.section-head{left:0;width:1200px;text-align:center}
.section-head h2{font-family:'Great Vibes',cursive;font-weight:400;color:var(--teal);font-size:54px;line-height:60px}
.section-head .tagline{font-size:13.5px;letter-spacing:2.6px;color:var(--muted);margin-top:44px}
.divider{left:532px;top:1000px;width:136px;height:8px}

.card{width:414px;height:352px;background:var(--white);border-radius:8px;box-shadow:0 3px 14px rgba(0,0,0,.1);overflow:hidden}
.card .photo{position:relative;height:240px}
.card .photo h3{position:absolute;left:20px;bottom:20px;font-family:'Dancing Script',cursive;font-weight:500;font-size:30px;color:var(--white)}
.card .photo h3 small{display:block;font-family:'Montserrat',sans-serif;font-size:13px;letter-spacing:2px;font-weight:600;margin-top:-4px}
.card p{margin:20px 20px 0;font-size:15px;line-height:19px;color:var(--muted)}
.card .explore{position:absolute;left:20px;bottom:22px;font-size:13.5px;letter-spacing:1px;font-weight:600;color:var(--teal);display:flex;align-items:center;gap:10px}
.photo-castle{background:linear-gradient(180deg,#e8e6e2 0%,#a9b8cf 45%,#6f6a6c 100%)}
.photo-beach{background:linear-gradient(180deg,#3f7f9a 0%,#45b3b7 45%,#c7b9a8 100%)}
.photo-road{background:linear-gradient(180deg,#2b6f95 0%,#3b6b7a 50%,#7a5a3c 100%)}
.photo-signs{background:linear-gradient(180deg,#8fb6d8 0%,#5e8ea0 45%,#8a7357 100%)}

.cta{left:0;top:1875px;width:1200px;height:347px;background:var(--teal);color:var(--white);text-align:center}
.cta .eyebrow{position:absolute;left:0;width:1200px;top:80px;font-size:15px;letter-spacing:3px}
.cta h2{position:absolute;left:0;width:1200px;top:100px;font-family:'Dancing Script',cursive;font-weight:500;font-size:52px}
.cta p{position:absolute;left:330px;width:540px;top:178px;font-size:16.5px;line-height:17px}
.cta .btn{position:absolute;left:504px;top:238px;width:192px;height:43px;line-height:43px}

.footer-brand{left:125px;top:2300px;display:flex;align-items:center;gap:8px;color:var(--teal);font-size:20px;font-weight:600;width:150px;line-height:1.2}
.footer-brand .dot{width:18px;height:18px;border-radius:50%;background:var(--gold);flex:none}
.footer-about{left:125px;top:2446px;width:270px;font-size:15.5px;line-height:18px;color:var(--teal);letter-spacing:.3px}
.footer-col h4{font-weight:500;font-size:20px;color:var(--teal);margin-bottom:22px}
.footer-col ul{list-style:none;font-size:15.5px;color:var(--teal);letter-spacing:.3px}
.footer-col li{height:25px}
.reach li{display:flex;align-items:center;gap:6px}
.reach .social{margin-top:12px;display:flex;gap:20px;font-size:14px;color:var(--gold);font-weight:600}
.copyright{left:0;width:1200px;top:2577px;text-align:center;font-size:13.5px;color:var(--teal)}
</style>
</head>
<body>

<div class="abs topbar">
  <div class="abs contact">
    <span><svg width="12" height="12" viewBox="0 0 24 24"><path fill="#c9a444" d="M6.6 10.8a15.1 15.1 0 0 0 6.6 6.6l2.2-2.2a1 1 0 0 1 1-.25 11.4 11.4 0 0 0 3.6.57 1 1 0 0 1 1 1V20a1 1 0 0 1-1 1A17 17 0 0 1 3 4a1 1 0 0 1 1-1h3.5a1 1 0 0 1 1 1c0 1.25.2 2.45.57 3.570a1 1 0 0 1-.25 1z"/></svg>555.010.2040</span>
    <span><svg width="15" height="11" viewBox="0 0 24 18"><rect width="24" height="18" rx="2" fill="#c9a444"/><path d="M1 2l11 8 11-8" stroke="#1e6f6c" stroke-width="2" fill="none"/></svg>HumAlongRoam@mailbox.com</span>
  </div>
  <div class="abs social"><a href="#">Circlebook</a><a href="#">Lensgram</a></div>
</div>

<header class="abs header"></header>
<a class="abs brand" href="#"><span class="dot"></span>Hum Along As You Roam</a>
<nav class="abs nav">
  <a class="active" href="#">HOME</a><a href="#">BRIMWELL</a><a href="#">FAMILY TRIPS</a><a href="#">ROAD TRIPS</a><a href="#">OTHER</a><a href="#">ABOUT</a><a href="#">CONTACT</a>
</nav>

<section class="abs hero" role="img" aria-label="Mountain lake with forested slopes and rowboats, tinted teal">
  <div class="rule" style="top:133px"></div>
  <div class="eyebrow">WELCOME TO</div>
  <div class="rule" style="top:173px"></div>
  <h1>Hum Along As You<br>Roam</h1>
  <div class="sub">TRAVEL CO.</div>
  <p>Let us help you plan the perfect vacation. From Brimwell magic to family road trips, every journey begins with a single step.</p>
  <a class="btn" href="#">START PLANNING TODAY</a>
</section>
<svg class="abs wave" viewBox="0 0 1200 42" preserveAspectRatio="none"><path d="M0 38 C200 18 330 12 520 22 S900 22 1200 8 V42 H0Z" fill="#fff"/></svg>

<div class="abs section-head" style="top:920px">
  <h2>Our Destinations</h2>
  <div class="tagline">CHOOSE YOUR NEXT ADVENTURE</div>
</div>
<svg class="abs divider" viewBox="0 0 136 8"><line x1="0" y1="4" x2="54" y2="4" stroke="#c9a444"/><line x1="82" y1="4" x2="136" y2="4" stroke="#c9a444"/><path d="M68 0l2 4-2 4-2-4z" fill="#c9a444"/></svg>

<article class="abs card" style="left:173px;top:1083px">
  <div class="photo photo-castle" role="img" aria-label="Fairy-tale castle with crowds of visitors"><h3>Brimwell Vacations</h3></div>
  <p>From Starlight Castle to the open seas, we make Brimwell magic for your family.</p>
  <a class="explore" href="#">EXPLORE</a>
</article>
<article class="abs card" style="left:613px;top:1083px">
  <div class="photo photo-beach" role="img" aria-label="Family exploring a tropical beach together"><h3>Family Trips<small>CREATE MEMORIES</small></h3></div>
  <p>Curated family getaways designed to bring everyone together for unforgettable adventures.</p>
  <a class="explore" href="#">EXPLORE <svg width="22" height="8" viewBox="0 0 22 8"><path d="M0 4h20M17 1l3 3-3 3" stroke="#1e6f6c" stroke-width="1.3" fill="none"/></svg></a>
</article>
<article class="abs card" style="left:173px;top:1454px">
  <div class="photo photo-road" role="img" aria-label="Friends resting in the open trunk of a car at sunset"><h3>Road Trips from Texas</h3></div>
  <p>Scenic drives and hidden gems across Texas. Partnership with Piney Trail Van Rentals.</p>
  <a class="explore" href="#">EXPLORE</a>
</article>
<article class="abs card" style="left:613px;top:1454px">
  <div class="photo photo-signs" role="img" aria-label="Wooden signpost with city distances on a beach"><h3>Other Destinations</h3></div>
  <p>From tropical beaches to mountain retreats, the world awaits you.</p>
  <a class="explore" href="#">EXPLORE</a>
</article>

<section class="abs cta">
  <div class="eyebrow">READY?</div>
  <h2>Your Adventure Awaits</h2>
  <p>Whether it's a Brimwell dream or a Texas road trip, we're here to make it happen.</p>
  <a class="btn" href="#">CONTACT US</a>
</section>

<a class="abs footer-brand" href="#"><span class="dot"></span>Hum Along As You Roam</a>
<p class="abs footer-about">Helping families create magical memories through expertly planned vacations and road trips.</p>

<div class="abs footer-col" style="left:526px;top:2300px">
  <h4>Quick links</h4>
  <ul><li>Home</li><li>Brimwell</li><li>Family Trips</li><li>Road Trips</li><li>Other</li><li>About</li><li>Contact</li></ul>
</div>
<div class="abs footer-col reach" style="left:748px;top:2300px">
  <h4>Reach Out</h4>
  <ul>
    <li><svg width="14" height="14" viewBox="0 0 24 24"><path fill="#c9a444" d="M6.6 10.8a15.1 15.1 0 0 0 6.6 6.6l2.2-2.2a1 1 0 0 1 1-.25 11.4 11.4 0 0 0 3.6.57 1 1 0 0 1 1 1V20a1 1 0 0 1-1 1A17 17 0 0 1 3 4a1 1 0 0 1 1-1h3.5a1 1 0 0 1 1 1c0 1.25.2 2.45.57 3.57a1 1 0 0 1-.25 1z"/></svg>555.010.2040</li>
    <li><svg width="15" height="11" viewBox="0 0 24 18"><rect width="24" height="18" rx="2" fill="#c9a444"/><path d="M1 2l11 8 11-8" stroke="#fff" stroke-width="2" fill="none"/></svg>HumAlongRoam@mailbox.com</li>
  </ul>
  <div class="social"><span>Circlebook</span><span>Lensgram</span></div>
</div>

<p class="abs copyright">© 2026 Hum Along As You Roam Travel Co. All rights reserved.</p>

</body>
</html>
```